Quillmarsh Property Solutions need a business card design

Hello guys. We would need a business card design asap please.
We are a start up property investment business based in London UK specialised in buying, selling, managing and letting properties and helping distressed property owners.
The name of our Business is Quillmarsh, the logo symbolises the four fundamental elements of the world (earth, air, fire and water) and so it stands for strength, stability, longevity.
We would like the business card to communicate professionalism and reliability. Many many thanks indeed for your work.

Details:

1.) Rosalind Updike
Property Investor
Mobile: +44(0)7700123456
Email: rosalind.quillmarsh@mailbox-example.com

2.) Dominic Updike
Property Investor
Mobile: +44(0)7700987654
Email: dominic.quillmarsh@mailbox-example.com

```html
<!DOCTYPE html>
<html lang="en">
<head>
<meta charset="utf-8">
<title>Quillmarsh Property Solutions – Business Card</title>
<link href="https://fonts.googleapis.com/css2?family=Open+Sans:wght@400;600;700&display=swap" rel="stylesheet">
<style>
  :root {
    --backdrop: #9a9b9c;
    --card: #eceeef;
    --ink: #2b2d30;
    --ink-soft: #5d6065;
    --accent: #3f8ff0;
    --accent-light: #7db4f7;
    --logo-mark: #4a7fd8;
  }
  * { margin: 0; padding: 0; box-sizing: border-box; }
  html, body {
    width: 1200px; height: 894px; overflow: hidden;
    background: var(--backdrop);
    font-family: "Open Sans", Arial, sans-serif;
  }
  .sheet {
    width: 1200px; height: 894px;
    display: flex; flex-direction: column; align-items: center; justify-content: center;
    gap: 36px;
  }
  .card {
    position: relative;
    width: 700px; height: 400px;
    background: var(--card);
    border-top: 4px solid var(--accent);
    overflow: hidden;
    box-shadow: 0 10px 24px rgba(0,0,0,.25);
  }
  .edge-tab {
    position: absolute;
    background: linear-gradient(90deg, var(--accent), var(--accent-light));
  }
  .card--front .edge-tab { left: 0; top: 118px; width: 54px; height: 40px; }
  .card--back .edge-tab { right: 0; top: 190px; width: 26px; height: 44px; }

  .brand { display: flex; align-items: center; gap: 12px; color: var(--ink); font-weight: 700; }
  .brand__mark { width: 28px; height: 28px; background: var(--logo-mark); }
  .brand__name { font-size: 22px; line-height: 1.05; letter-spacing: .5px; text-transform: uppercase; }
  .brand__name small { display: block; font-size: 10px; letter-spacing: 1px; }

  .card--front .brand { position: absolute; left: 90px; top: 76px; }
  .person { position: absolute; left: 80px; top: 170px; }
  .person__name { font-size: 34px; font-weight: 700; color: var(--ink); letter-spacing: 1px; text-transform: uppercase; line-height: 1.1; }
  .person__role { font-size: 17px; color: var(--ink-soft); letter-spacing: 6px; text-transform: uppercase; }

  .contact { position: absolute; right: 60px; bottom: 44px; list-style: none; }
  .contact li { display: flex; align-items: flex-start; gap: 12px; font-size: 13px; font-weight: 600; color: var(--ink); line-height: 1.3; margin-top: 7px; }
  .contact svg { width: 16px; height: 16px; flex: none; fill: var(--ink); }

  .card--back .brand { position: absolute; left: 50%; top: 110px; transform: translateX(-50%); }
  .social { position: absolute; left: 60px; right: 60px; bottom: 72px; display: flex; justify-content: space-between; list-style: none; }
  .social li { display: flex; align-items: center; gap: 10px; font-size: 15px; color: var(--ink-soft); }
  .social__mark { width: 22px; height: 22px; background: var(--ink); }
</style>
</head>
<body>
<main class="sheet">
  <section class="card card--front" aria-label="Business card front">
    <span class="edge-tab"></span>
    <div class="brand">
      <span class="brand__mark"></span>
      <span class="brand__name">Quillmarsh<small>Property Solutions</small></span>
    </div>
    <div class="person">
      <h1 class="person__name">Marcus Penhallow</h1>
      <p class="person__role">General Manager</p>
    </div>
    <ul class="contact">
      <li>
        <svg viewBox="0 0 16 16" aria-hidden="true"><path d="M8 1 0 8h2v7h4v-4h4v4h4V8h2z"/></svg>
        <span>14 Fenwick Court,<br>Harrow Lane NW3</span>
      </li>
      <li>
        <svg viewBox="0 0 16 16" aria-hidden="true"><path d="M8 1a7 7 0 1 0 0 14A7 7 0 0 0 8 1zm0 1.5c.8 0 1.7 1.5 2 4H6c.3-2.5 1.2-4 2-4zM2.6 6.5h2c-.1 1 0 2 0 3h-2a5.6 5.6 0 0 1 0-3zm3.4 0h4c.1 1 .1 2 0 3H6c-.1-1-.1-2 0-3zm5.4 0h2a5.6 5.6 0 0 1 0 3h-2c.1-1 .1-2 0-3zM6 11h4c-.3 2.5-1.2 3.5-2 3.5S6.3 13.5 6 11z"/></svg>
        <span>www.quillmarsh-example.com</span>
      </li>
      <li>
        <svg viewBox="0 0 16 16" aria-hidden="true"><path d="M0 3h16v1L8 9 0 4zm0 2.5 8 5 8-5V13H0z"/></svg>
        <span>yourname@mailbox-example.com</span>
      </li>
      <li>
        <svg viewBox="0 0 16 16" aria-hidden="true"><path d="M4 1 6 5 4.5 6.5c.8 1.8 2.2 3.2 4 4L10 9l4 2-1 3c-6 0-12-6-12-12z"/></svg>
        <span>012 345 6789</span>
      </li>
    </ul>
  </section>

  <section class="card card--back" aria-label="Business card back">
    <span class="edge-tab"></span>
    <div class="brand">
      <span class="brand__mark"></span>
      <span class="brand__name">Quillmarsh<small>Property Solutions</small></span>
    </div>
    <ul class="social">
      <li><span class="social__mark"></span>yourname</li>
      <li><span class="social__mark"></span>@yourname</li>
      <li><span class="social__mark"></span>yourname</li>
    </ul>
  </section>
</main>
</body>
</html>
```